Firm-Asset: Tomorrow - EU-funded management consulting

A website to inform possible customers about my management consulting services for small and medium sized companies. I am using a funding for small and medium companies to do 10 days of workshops and coaching about leadership, further education and employee's health. The Funding is called "Betriebsgut Zukunft" which means something like: Humans are the value of the company. The official logo is attached as a

Target Market(s)

Small and medium sized companies that want to improve their employee's well being and efficiency.

Industry/Entity Type

Management Consulting

Contact Information for Business Card

Malte Quast, Birkenhainweg 14, 10219 Berlin

Logo Text

BetriebsGut Zukunft - Beratung

Font styles to use
Serif
Sans Serif

Requirements
Must have
• a friendly and professional design
Nice to have
• saying somthing about: employees, leadership, further education and employees health are important to us.
Should not have
• should not be too shimmering

```html
<!DOCTYPE html>
<html lang="en">
<head>
<meta charset="utf-8">
<title>Betriebsgut Zukunft – Beratung</title>
<link href="https://fonts.googleapis.com/css2?family=Open+Sans:wght@400;600;700;800&display=swap" rel="stylesheet">
<style>
:root{
  --orange:#e8772e;
  --dark:#2b2b2b;
  --text:#555;
  --light:#f2f2f2;
  --line:#e3e3e3;
  --footer:#232323;
  --navy:#1f3f73;
  --white:#fff;
}
*{margin:0;padding:0;box-sizing:border-box}
html,body{width:755px;height:1200px;overflow:hidden}
body{font-family:"Open Sans",Arial,sans-serif;color:var(--text);background:var(--white);position:relative;font-size:8px;line-height:1.5}
.site-header{height:62px;display:flex;align-items:center;justify-content:space-between;padding:0 60px 0 62px;border-bottom:1px solid var(--line)}
.brand{display:flex;align-items:center;gap:6px;font-weight:700;font-size:12px;color:var(--navy)}
.brand-mark{width:12px;height:12px;background:var(--navy)}
.main-nav{display:flex;gap:22px;font-size:7px;font-weight:600;color:var(--dark);text-transform:uppercase}
.main-nav .active{color:var(--orange)}
.hero{position:relative;height:318px;background:
  linear-gradient(180deg,rgba(255,255,255,0) 45%,rgba(40,52,72,.55) 100%),
  linear-gradient(100deg,#dfe3e8 0%,#f6f7f8 30%,#e6e9ec 55%,#cfd5dc 80%,#bfc6cf 100%)}
.hero-caption{position:absolute;left:88px;top:228px;width:430px;background:rgba(25,25,25,.8);padding:11px 16px 12px;color:var(--white)}
.hero-caption h1{font-size:15px;font-weight:700;letter-spacing:.3px;margin-bottom:5px}
.hero-caption p{font-size:7.5px;color:#ddd}
.hero-dots{position:absolute;right:22px;bottom:12px;display:flex;gap:4px}
.hero-dots span{width:9px;height:9px;background:rgba(255,255,255,.7)}
.section-title{text-align:center;font-size:13px;font-weight:700;color:var(--dark)}
.section-sub{text-align:center;font-size:7.5px;color:var(--orange);font-weight:600;margin-top:4px;text-transform:uppercase}
.services{height:218px;padding-top:20px;border-bottom:1px solid var(--line)}
.service-cards{display:flex;justify-content:center;gap:24px;margin-top:20px}
.service-card{width:190px;height:118px;display:flex;gap:8px;border:1px solid var(--line);padding:6px;background:var(--white)}
.service-photo{width:82px;height:104px;flex:none;background:linear-gradient(160deg,#d9dde2,#b9c0c8)}
.service-card h3{font-size:8.5px;font-weight:700;color:var(--dark);margin-top:4px;text-transform:uppercase;line-height:1.25}
.service-card h3 small{display:block;color:var(--orange);font-size:7px;font-weight:600}
.service-card p{font-size:6.5px;margin-top:4px}
.service-card a{display:block;color:var(--orange);font-size:6.5px;font-weight:600;margin-top:4px;text-decoration:none}
.what-we-do{height:236px;background:var(--light);display:flex;padding:0 52px 0 50px;align-items:flex-end}
.team-photo{width:300px;height:214px;flex:none;background:linear-gradient(180deg,#e4e6e9,#9ea5ae)}
.what-copy{flex:1;align-self:center;padding-left:34px}
.what-copy .section-title,.what-copy .section-sub{text-align:left}
.what-copy p{font-size:7px;margin-top:10px}
.feature-row{display:flex;gap:26px;margin-top:20px}
.feature{display:flex;align-items:center;gap:8px}
.feature svg{flex:none}
.feature strong{display:block;color:var(--orange);font-size:7px;font-weight:600}
.feature span{font-size:6.5px}
.info{height:252px;display:flex;gap:36px;padding:22px 52px 0 62px}
.info-col{flex:1}
.info h2{font-size:12px;font-weight:700;color:var(--dark);padding-bottom:6px;border-bottom:1px solid var(--line);margin-bottom:10px}
.info p{font-size:7px;margin-bottom:8px}
.about-media{display:flex;gap:12px;margin-top:6px}
.about-photo{width:100px;height:78px;flex:none;background:linear-gradient(150deg,#dfe2e5,#b4bac2)}
.quote{border-left:2px solid var(--orange);padding-left:10px}
.quote cite{display:block;text-align:right;font-style:normal;font-size:7px;color:var(--dark);font-weight:600}
.quote cite small{display:block;color:var(--orange);font-weight:400}
.client-strip{display:flex;gap:3px;margin-top:10px}
.client-strip span{width:26px;height:26px;background:linear-gradient(160deg,#c6cbd1,#8e959e)}
.site-footer{position:absolute;left:0;right:0;bottom:0;height:112px;background:var(--footer);color:#aaa;text-align:center;padding-top:22px}
.social{display:flex;justify-content:center;gap:8px}
.social span{width:20px;height:20px;border-radius:50%;border:1px solid #777}
.footer-nav{display:flex;justify-content:center;gap:18px;font-size:6.5px;text-transform:uppercase;margin-top:16px}
.copyright{font-size:6px;margin-top:8px;color:#888}
</style>
</head>
<body>
<header class="site-header">
  <div class="brand"><span class="brand-mark"></span>Betriebsgut Zukunft</div>
  <nav class="main-nav"><span class="active">Home</span><span>About Us</span><span>Services</span><span>News</span><span>Testimonials</span><span>Contact Us</span></nav>
</header>

<section class="hero" role="img" aria-label="Photo of a smiling business team in office wear">
  <div class="hero-caption">
    <h1>WELCOME TO OUR COMPANY</h1>
    <p>We are a consulting team that helps small and medium sized companies grow with strong leaders, healthy teams and learning that lasts.</p>
  </div>
  <div class="hero-dots"><span></span><span></span></div>
</section>

<section class="services">
  <h2 class="section-title">OUR SERVICES</h2>
  <div class="section-sub">We offer services to small and medium sized companies</div>
  <div class="service-cards">
    <article class="service-card">
      <div class="service-photo" role="img" aria-label="Photo of a leadership workshop"></div>
      <div><h3>Workshops &amp;<small>Leadership</small></h3><p>Clear goals, good feedback and calm decisions for leaders in every team.</p><a href="#">Read More »</a></div>
    </article>
    <article class="service-card">
      <div class="service-photo" role="img" aria-label="Photo of a healthy employee"></div>
      <div><h3>Employees &amp;<small>Health</small></h3><p>Simple habits that keep people fit, focused and happy at their work.</p><a href="#">Read More »</a></div>
    </article>
    <article class="service-card">
      <div class="service-photo" role="img" aria-label="Photo of colleagues learning together"></div>
      <div><h3>Further<small>Education</small></h3><p>Courses and coaching that help staff learn new skills step by step.</p><a href="#">Read More »</a></div>
    </article>
  </div>
</section>

<section class="what-we-do">
  <div class="team-photo" role="img" aria-label="Photo of a group of business people standing together"></div>
  <div class="what-copy">
    <h2 class="section-title">WHAT WE DO</h2>
    <div class="section-sub">Ten funded days for stronger teams and leaders</div>
    <p>Over ten funded days we work with your company on leadership, further education and employee health. We listen first, then build workshops and coaching that fit your people, your goals and your daily routine.</p>
    <div class="feature-row">
      <div class="feature">
        <svg width="22" height="22" viewBox="0 0 22 22"><circle cx="11" cy="11" r="10.5" fill="#fff" stroke="#e3e3e3"/><path d="M7 15l7-7m-4 0h4v4" stroke="#e8772e" stroke-width="1.5" fill="none"/></svg>
        <div><strong>Company Funding</strong><span>Click here</span></div>
      </div>
      <div class="feature">
        <svg width="22" height="22" viewBox="0 0 22 22"><circle cx="11" cy="11" r="10.5" fill="#fff" stroke="#e3e3e3"/><path d="M7 11.5l3 3 5-6" stroke="#e8772e" stroke-width="1.5" fill="none"/></svg>
        <div><strong>Company Coaching</strong><span>Click here</span></div>
      </div>
    </div>
  </div>
</section>

<section class="info">
  <div class="info-col">
    <h2>About our Company</h2>
    <p>We support owners and managers who want a workplace where people feel valued and do their best work every day.</p>
    <div class="about-media">
      <div class="about-photo" role="img" aria-label="Photo of a consultant at work"></div>
      <p>Our coaching is practical, friendly and built around the real questions your team faces.</p>
    </div>
  </div>
  <div class="info-col">
    <h2>Our Testimonials</h2>
    <div class="quote">
      <p>The workshops gave our leaders new confidence and our team talks more openly now. The coaching was clear, warm and always close to our daily work.</p>
      <cite>Anna Becker<small>Managing Director</small></cite>
    </div>
    <div class="client-strip" role="img" aria-label="Row of client portrait photos"><span></span><span></span><span></span><span></span><span></span><span></span><span></span><span></span><span></span></div>
  </div>
</section>

<footer class="site-footer">
  <div class="social"><span></span><span></span><span></span><span></span><span></span></div>
  <nav class="footer-nav"><span>Home</span><span>About Us</span><span>Services</span><span>News</span><span>Testimonials</span><span>Contact Us</span></nav>
  <div class="copyright">© Copyright 2014 Betriebsgut Zukunft. All Rights Reserved.</div>
</footer>
</body>
</html>
```